Wandering Rooms Stationary Set

Wandering Rooms is a bespoke interior design firm set to provide services to VIP clients with elegance and minimalism is the main theme for our stationary set. We require a full stationary set covering A4 letterhead, A4 & A3 envelopes, business cards, USB's, CDs, email signature and any other item the designer sees fit. logo is already designed and finalized, and we require the designer to use it as is without modifying the logo.

Address to be used on letterhead / business cards ...etc shall be as follows:

Phone : +971 2 518 2047
P.O. Box : 309186
Address: Block C&D, Bldg. 47, Court 12, Abu Dhabi, United Arab Emirates
Website: www.wanderingrooms-example.com

Target Market(s)

VIP Clients

Industry/Entity Type

Interior Design

Font styles to use
Other font styles liked:
• something to be unique

Colors

Designer to choose colors to be used in the design.

Requirements
Must have
• Elegant, minimalistic
Nice to have
• Simple yet elegant design having a sharp yet clean cut format
Should not have
• No additional colours, just colours that are used in the logo (silver, black or gold)

```html
<!DOCTYPE html>
<html lang="en">
<head>
<meta charset="utf-8">
<title>Wandering Rooms – Business Card</title>
<link rel="stylesheet" href="https://fonts.googleapis.com/css2?family=Cormorant+Garamond:wght@400;500;600;700&display=swap">
<style>
  :root {
    --backdrop: #ececec;
    --card-dark: #232323;
    --card-dark-deep: #1b1b1b;
    --card-light: #ffffff;
    --ink-light: #ffffff;
    --ink-dark: #1e1e1e;
    --serif: "Cormorant Garamond", Garamond, Georgia, serif;
  }
  * { box-sizing: border-box; margin: 0; padding: 0; }
  html, body { width: 1200px; height: 757px; overflow: hidden; }
  body {
    position: relative;
    background: var(--backdrop);
    font-family: var(--serif);
  }

  .card {
    position: absolute;
    top: 195px;
    width: 499px;
    height: 299px;
    overflow: hidden;
  }
  .card--front { left: 90px; background: var(--card-light); }
  .card--back  { left: 650px; background: var(--card-dark); }

  .texture {
    position: absolute;
    background: linear-gradient(135deg, var(--card-dark) 0%, var(--card-dark-deep) 55%, var(--card-dark) 100%);
  }
  .card--front .texture { left: 0; top: 0; width: 499px; height: 264px; }
  .card--back .texture  { left: 167px; top: 0; width: 332px; height: 299px; }

  /* Front */
  .front-brand {
    position: absolute;
    left: 0; right: 0;
    top: 112px;
    text-align: center;
    color: var(--ink-light);
    font-size: 40px;
    font-weight: 500;
    letter-spacing: 1px;
  }
  .front-web {
    position: absolute;
    left: 0; right: 0;
    top: 264px;
    height: 35px;
    line-height: 35px;
    text-align: center;
    color: var(--ink-dark);
    font-size: 12px;
    font-weight: 700;
    letter-spacing: 2px;
  }

  /* Back */
  .brand-strip {
    position: absolute;
    left: 0; top: 0;
    width: 167px; height: 299px;
    background: var(--card-light);
    display: flex;
    align-items: center;
    justify-content: center;
  }
  .brand-strip__name {
    writing-mode: vertical-rl;
    color: var(--ink-dark);
    font-size: 34px;
    font-weight: 500;
    letter-spacing: 1px;
  }

  .holder {
    position: absolute;
    right: 35px;
    top: 40px;
    padding-right: 10px;
    border-right: 2px solid var(--ink-light);
    text-align: right;
    color: var(--ink-light);
  }
  .holder__name { font-size: 17px; font-weight: 500; line-height: 20px; }
  .holder__role { font-size: 11px; font-weight: 500; line-height: 14px; }

  .address {
    position: absolute;
    right: 31px;
    top: 126px;
    text-align: right;
    color: var(--ink-light);
    font-size: 12.5px;
    font-weight: 700;
    line-height: 17px;
  }

  .contacts {
    position: absolute;
    right: 31px;
    top: 214px;
    list-style: none;
    color: var(--ink-light);
    font-size: 10.5px;
    font-weight: 700;
  }
  .contacts li {
    display: flex;
    justify-content: flex-end;
    align-items: center;
    gap: 10px;
    height: 21px;
  }
  .contacts svg { width: 15px; height: 15px; display: block; }
</style>
</head>
<body>

  <section class="card card--front" aria-label="Business card front">
    <div class="texture" role="img" aria-label="Dark faceted polygon background texture"></div>
    <div class="front-brand">Wandering Rooms</div>
    <div class="front-web">www.wanderingrooms-example.com</div>
  </section>

  <section class="card card--back" aria-label="Business card back">
    <div class="brand-strip">
      <span class="brand-strip__name">Wandering Rooms</span>
    </div>
    <div class="texture" role="img" aria-label="Dark faceted polygon background texture"></div>

    <div class="holder">
      <div class="holder__name">Layla Farouk</div>
      <div class="holder__role">Director</div>
    </div>

    <div class="address">
      <div>Block C&amp;D, Bldg. 47</div>
      <div>Court 12, Abu Dhabi, United Arab Emirates</div>
    </div>

    <ul class="contacts">
      <li>
        <span>+971 2 518 2047</span>
        <svg viewBox="0 0 16 16" aria-hidden="true">
          <circle cx="8" cy="8" r="8" fill="#fff"/>
          <path d="M5.2 4.2l1.5-.3.8 2-1 .8a5 5 0 0 0 2.8 2.8l.8-1 2 .8-.3 1.5c-3.6.2-6.8-3-6.6-6.6z" fill="#232323"/>
        </svg>
      </li>
      <li>
        <span>lfarouk@wanderingrooms-example.com</span>
        <svg viewBox="0 0 16 16" aria-hidden="true">
          <circle cx="8" cy="8" r="8" fill="#fff"/>
          <rect x="4" y="5" width="8" height="6" fill="none" stroke="#232323" stroke-width="1.2"/>
          <path d="M4 5l4 3.2L12 5" fill="none" stroke="#232323" stroke-width="1.2"/>
        </svg>
      </li>
      <li>
        <span>P.O. Box : 309186</span>
        <svg viewBox="0 0 16 16" aria-hidden="true">
          <circle cx="8" cy="8" r="8" fill="#fff"/>
          <rect x="4" y="5" width="8" height="6" fill="#232323"/>
          <path d="M4.4 5.4L8 8.2l3.6-2.8" fill="none" stroke="#fff" stroke-width="0.9"/>
        </svg>
      </li>
    </ul>
  </section>

</body>
</html>
```